Coffee Bag Label design for Australian Firefighter brand

I need a label for coffee bags. Front and back. We are based in Australia and aimed at Firefighters and First responders. I will have three size available. 250g, 500g and 1kg. So if we can use the same label that would be great. maybe a check box option at the bottom with the three sizes.
I really like the design for Lanyard Coffee (see attached), so I'm hoping for something along the same lines. replacing the images with firefighter axe, hose, halagan tool, cutting gear etc
I would like to include 'Firefighter founded" on the front, as well as 'Copper Ridge Blend'. Roasted med-dark on the Sunshine Coast, QLD
On the back I need space for a qr code with an arrow pointing to it with handwritten font 'how're you travelling? Free, confidential wellness check in'
and the text;
Coffee without the b.s.
This ain’t the sort of coffee for your average piccolo drinking, man-bun enthusiast. No fancy rose petal and unicorn pube infusions here. Just consistently great coffee that shows up, for those who show up. Firefighter founded and built with the Australian First Responder in mind.
Your life is complicated enough. Your coffee shouldn’t be.
For more, go to bluekettleroast.com.au or scan the QR code for a free, fast, confidential mental wellness check-in and useful resources.
These will be printed as sticker lables to go on kraft black coffee bags to begin with. Please see attached bag example and logo for use.
Target Market(s)
Australian Firefighters and First responders
Look and feel

```html
<!DOCTYPE html>
<html lang="en">
<head>
<meta charset="utf-8">
<title>Blue Kettle Roast Co — Coffee Bag Labels</title>
<link rel="stylesheet" href="https://fonts.googleapis.com/css2?family=Oswald:wght@300;400;500;600;700&display=swap">
<style>
  :root {
    --page: #f1f1ef;
    --label: #2a2a2b;
    --label-edge: #232324;
    --ink-white: #f4f4f2;
    --ink-dark: #3a3a3b;
    --red: #e0353d;
    --red-band: #d8343c;
    --tool-light: #d9d9d7;
    --tool-dark: #4a4a4b;
  }
  * { box-sizing: border-box; margin: 0; padding: 0; }
  html, body { width: 1200px; height: 5110px; overflow: hidden; background: var(--page); }
  body { position: relative; font-family: "Oswald", "Arial Narrow", sans-serif; }

  .label {
    position: absolute; left: 210px; width: 780px; height: 1320px;
    background: var(--label); border-radius: 22px; overflow: hidden;
    box-shadow: inset 0 0 0 2px var(--label-edge);
  }
  .label--front-a { top: 170px; }
  .label--front-b { top: 1880px; }
  .label--back { top: 3620px; }

  .brand { position: absolute; left: 0; right: 0; top: 250px; display: flex; justify-content: center; align-items: center; gap: 16px; }
  .brand__name { color: var(--ink-white); font-weight: 600; font-size: 50px; letter-spacing: 1px; text-transform: uppercase; line-height: 1; }
  .brand__dot { width: 30px; height: 30px; border-radius: 50%; background: var(--red); }

  .blend { position: absolute; left: 30px; top: 520px; width: 450px; height: 250px; background: var(--red-band); padding: 24px 20px 0 22px; }
  .blend__line1 { color: var(--ink-dark); font-weight: 700; font-size: 118px; line-height: 1; letter-spacing: -1px; text-transform: uppercase; }
  .blend__line2 { color: var(--ink-white); font-weight: 700; font-size: 64px; line-height: 1.15; text-transform: uppercase; }
  .blend__line2 span { color: var(--ink-dark); }

  .art { position: absolute; border-radius: 10px; background: linear-gradient(160deg, var(--tool-light) 0%, var(--tool-dark) 100%); opacity: .55; }
  .art--extinguisher-front { left: 560px; top: 520px; width: 200px; height: 520px; }
  .art--axe-front { left: 150px; top: 800px; width: 400px; height: 240px; }
  .art--extinguisher-back { left: 520px; top: 300px; width: 190px; height: 480px; }
  .art--axe-back { left: 420px; top: 1030px; width: 340px; height: 260px; }

  .founded { position: absolute; left: 0; right: 0; top: 1080px; text-align: center; color: var(--ink-white); font-weight: 600; font-size: 60px; line-height: 1; text-transform: uppercase; }
  .origin { position: absolute; left: 0; right: 0; top: 1160px; text-align: center; color: var(--red); font-weight: 600; font-size: 17px; line-height: 1.35; text-transform: uppercase; }
  .sizes { position: absolute; left: 0; right: 0; top: 1238px; display: flex; justify-content: center; gap: 38px; }
  .size { display: flex; align-items: center; gap: 12px; color: var(--ink-white); font-weight: 600; font-size: 17px; }
  .size__box { width: 28px; height: 28px; border-radius: 4px; background: var(--ink-white); }

  .headline { position: absolute; left: 80px; top: 80px; }
  .headline__big { color: var(--red); font-weight: 700; font-size: 112px; line-height: 1; text-transform: uppercase; }
  .headline__sub { color: var(--ink-white); font-weight: 600; font-size: 54px; line-height: 1.1; text-transform: uppercase; margin-top: 8px; }

  .story { position: absolute; left: 100px; top: 320px; width: 400px; height: 640px; border: 3px solid var(--red); border-radius: 12px; padding: 28px 26px; }
  .story p { color: var(--ink-white); font-weight: 300; font-size: 21px; line-height: 1.3; }

  .pointer { position: absolute; left: 330px; top: 800px; }
  .offduty { position: absolute; left: 560px; top: 820px; width: 190px; }
  .offduty__small { color: var(--ink-white); font-weight: 600; font-size: 28px; line-height: 1; text-transform: uppercase; }
  .offduty__big { color: var(--ink-white); font-weight: 700; font-size: 62px; line-height: 1; text-transform: uppercase; }
  .offduty__note { color: var(--red); font-weight: 600; font-size: 17px; line-height: 1.2; margin-top: 8px; }

  .address { position: absolute; left: 210px; top: 1200px; color: var(--ink-white); font-weight: 300; font-size: 18px; line-height: 1.3; }
</style>
</head>
<body>

  <section class="label label--front-a" aria-label="Front label">
    <div class="brand"><span class="brand__name">Blue Kettle Roast Co</span><span class="brand__dot"></span></div>
    <div class="blend"><div class="blend__line1">Copper</div><div class="blend__line2">Ridge <span>Blend</span></div></div>
    <div class="art art--extinguisher-front" role="img" aria-label="Sketched fire extinguisher illustration"></div>
    <div class="art art--axe-front" role="img" aria-label="Sketched firefighter axe illustration"></div>
    <div class="founded">Firefighter Founded</div>
    <div class="origin">Roasted med-dark on the<br>Sunshine Coast, QLD</div>
    <div class="sizes">
      <div class="size"><span class="size__box"></span>250G</div>
      <div class="size"><span class="size__box"></span>500G</div>
      <div class="size"><span class="size__box"></span>1KG</div>
    </div>
  </section>

  <section class="label label--front-b" aria-label="Front label">
    <div class="brand"><span class="brand__name">Blue Kettle Roast Co</span><span class="brand__dot"></span></div>
    <div class="blend"><div class="blend__line1">Copper</div><div class="blend__line2">Ridge <span>Blend</span></div></div>
    <div class="art art--extinguisher-front" role="img" aria-label="Sketched fire extinguisher illustration"></div>
    <div class="art art--axe-front" role="img" aria-label="Sketched firefighter axe illustration"></div>
    <div class="founded">Firefighter Founded</div>
    <div class="origin">Roasted med-dark on the<br>Sunshine Coast, QLD</div>
    <div class="sizes">
      <div class="size"><span class="size__box"></span>250G</div>
      <div class="size"><span class="size__box"></span>500G</div>
      <div class="size"><span class="size__box"></span>1KG</div>
    </div>
  </section>

  <section class="label label--back" aria-label="Back label">
    <div class="headline">
      <div class="headline__big">Coffee</div>
      <div class="headline__sub">Without the B.S.</div>
    </div>
    <div class="story">
      <p>This ain't the sort of coffee for your average piccolo drinking, man-bun enthusiast. No fancy rose petal and unicorn pube infusions here. Just consistently great coffee that shows up, for those who show up. Firefighter founded and built with the Australian First Responder in mind.<br>Your life is complicated enough. Your coffee shouldn't be.</p>
    </div>
    <div class="art art--extinguisher-back" role="img" aria-label="Sketched fire extinguisher illustration"></div>
    <svg class="pointer" width="230" height="110" viewBox="0 0 230 110" aria-hidden="true">
      <path d="M40 40 C10 30 10 70 40 60 C70 50 60 20 45 30 C90 10 160 20 205 80" fill="none" stroke="#f4f4f2" stroke-width="4" stroke-linecap="round"/>
      <path d="M185 82 L207 84 L200 62" fill="none" stroke="#f4f4f2" stroke-width="4" stroke-linecap="round" stroke-linejoin="round"/>
    </svg>
    <div class="offduty">
      <div class="offduty__small">Fit for off</div>
      <div class="offduty__big">Duty</div>
      <div class="offduty__note">Scan here for free firefighter wellness resources.</div>
    </div>
    <div class="art art--axe-back" role="img" aria-label="Sketched firefighter axe illustration"></div>
    <div class="address">27 Quarry Lane,<br>Ashvale, QLD</div>
  </section>

</body>
</html>
```